We need a modern WIX website for Brightform Beam Services Australia (Laser/Industrial/Engineering)

We need a website for Wix (coded) for our laser restoration and industrial cleaning business.

It will need to be 4-6 pages.
Pages may include:
Home
About
Why Laser
Capabilities
There needs to be a contact / quote form

We do not want boring institutional design, so please do try to be a little creative (but not artsy, more engineering / laser etc). We hesitate with boxy wordpress looking templates, so please bring in strip backgrounds and sliders etc;

Our brand colours are blue and red, but a sharp modern site relative to the industry and work is important.

We envision the home page to take visitors on a informed journey of who, what, why, how, explaining the capability of laser science across contaminants, industries and surfaces.

We envision the home page to be strips:
- landing
- intro

-Why choose laser / What is laser cleaning
Minimum downtime, no surface damage, no environmental impact, no mess, no waste, complete restoration (we have an explainer video)

- Contaminants
Bacteria, Rust, Corrosion, Oxides, Grease, Oil, Paint, Stains, Mold, Soot / Carbon, Graffiti, Coatings, Dirt, Residue

- Surfaces
Metals, Engines/Parts/Components, Tools, Machinery, Bricks/Blockwork, Concrete, Paint, Stone, Wood, Aluminium

- Industries
Medical/Sterile, Hospitality, Bio Hazardous, Construction, Infrastructure, Property, Industrial, Engineer, Automotive, Marine, Heritage, Non Destructive Testing,

----
Here is some info on the company below:

"Background Information - Brightform Beam Services Australia (BBSA) is a leading provider of advanced laser restoration services for the residential, commercial, medical, hazardous and industrial sectors, offering waste free, chemical free and damage free complete restoration of metals, concrete, wood, stone and heritage, hygiene and hazard surfaces, with complete removal of coatings, bacteria, paint, rust, graffiti, mold and fire ash (soot), and preparation and treating for welding and bonding.
Servicing Melbourne and Victoria, with additional services available Australia wide, BBSA offers a 24/7 call-out service to your site.
With no downtime to your operations, we offer a timely resolution to your cleaning and maintenance needs."

We have attached some inspiration of websites we like the flow/feel of, but feel free to put your best designs forward.

You are welcome to use dummy headers and text at this stage, as design and feel is most important, and we can add text later.

```html
<!DOCTYPE html>
<html lang="en">
<head>
<meta charset="utf-8">
<title>Brightform Beam Services Australia</title>
<link rel="stylesheet" href="https://fonts.googleapis.com/css2?family=Orbitron:wght@700;800&family=Open+Sans:wght@400;600;700&display=swap">
<style>
:root{
  --blue:#1a73c4;
  --red:#e8262d;
  --ink:#0b0c10;
  --dark:#14161b;
  --white:#ffffff;
  --muted:#d6d9e0;
  --display:'Orbitron',sans-serif;
  --body:'Open Sans',sans-serif;
}
*{margin:0;padding:0;box-sizing:border-box}
html,body{width:1200px;height:2893px;overflow:hidden;background:var(--ink)}
body{position:relative;font-family:var(--body);color:var(--white)}
.abs{position:absolute}
a{color:inherit;text-decoration:none}

/* header */
.site-header{left:0;top:0;width:1200px;height:92px;background:#0f1014}
.topbar{left:0;top:0;width:1200px;height:28px}
.topbar-text{right:112px;top:6px;font-size:12px;color:var(--white)}
.brand{left:112px;top:22px;display:flex;align-items:center;gap:12px;font-family:var(--body);font-weight:700;font-size:42px;letter-spacing:2px;color:var(--white);line-height:48px}
.brand-dot{width:20px;height:20px;border-radius:50%;background:var(--white)}
.nav{top:48px;display:flex;gap:20px;font-size:15.5px;color:var(--white);font-weight:600;white-space:nowrap}
.nav .sep{font-weight:400}
.btn{display:flex;align-items:center;justify-content:center;border-radius:5px;font-weight:600;font-size:16px;color:var(--white)}
.btn-blue{background:var(--blue)}
.btn-red{background:var(--red)}

/* hero */
.hero-photo{left:0;top:92px;width:1200px;height:483px;background:radial-gradient(ellipse at 62% 40%,#2fa3b0 0%,#1b5f6e 35%,#0f2e36 70%,#0a1216 100%)}
.hero-glow{left:0;top:300px;width:600px;height:230px;background:radial-gradient(ellipse at 45% 70%,rgba(255,176,64,.75) 0%,rgba(220,110,30,.35) 30%,rgba(0,0,0,0) 65%)}
.hero-kicker{left:0;top:232px;width:1200px;text-align:center;font-family:var(--display);font-weight:700;font-size:26px;letter-spacing:1px}
.hero-title{left:0;top:266px;width:1200px;text-align:center;font-family:var(--display);font-weight:800;font-size:35px;letter-spacing:1px;white-space:nowrap}
.hero-line{left:551px;top:317px;width:98px;height:3px;background:var(--blue)}

/* section heads */
.section-title{left:0;width:1200px;text-align:center;font-family:var(--display);font-weight:800;font-size:40px;letter-spacing:1px}
.rule{height:3px;width:54px}

/* about */
.about-bg{left:0;top:500px;width:1200px;height:557px;background:linear-gradient(90deg,#1f2a3a 0%,#2b3645 45%,#3a4553 70%,#1d2430 100%)}
.about-title{left:112px;top:606px;font-family:var(--display);font-weight:800;font-size:40px}
.about-text{left:112px;top:695px;width:473px;font-size:15.5px;line-height:28.3px;text-align:justify;color:var(--white)}
.about-photo{left:745px;top:647px;width:305px;height:334px;background:linear-gradient(160deg,#c9d6e2 0%,#7b6a52 40%,#3b3026 65%,#6f7f93 100%)}

/* why */
.why-bg{left:0;top:1057px;width:1200px;height:360px;background:linear-gradient(180deg,#121a2c 0%,#1a2640 60%,#0e1424 100%)}
.card{top:1218px;width:180px;height:95px;background:var(--white);border-radius:6px;display:flex;align-items:center;gap:12px;padding-left:24px;color:#1d2333;font-size:15.5px;line-height:21px}
.card svg{flex:none}

/* industries */
.ind-bg{left:0;top:1417px;width:1200px;height:556px;background:linear-gradient(180deg,#2a2020 0%,#3a3234 40%,#1b1a1e 100%)}
.ind-card{top:1592px;width:229px;height:312px}
.ind-blue{background:linear-gradient(180deg,#a9c6e0 0%,#4f87bf 55%,#1a73c4 100%)}
.ind-red{background:linear-gradient(180deg,#c9a49a 0%,#c85a55 50%,#e8262d 100%)}
.ind-label{left:20px;bottom:42px;font-size:19px;font-weight:600}
.arrow{top:1733px}

/* work on */
.work-bg{left:0;top:1973px;width:1200px;height:620px;background:radial-gradient(ellipse at 20% 80%,#5a1e14 0%,#200c0a 40%,#08080a 75%)}
.list-head{font-size:23px;font-weight:600}
.list{font-size:17px;line-height:27.4px;list-style:none}
.list li{display:flex;align-items:center;gap:13px}
.list li::before{content:"";width:6px;height:6px;border-top:1.5px solid var(--red);border-right:1.5px solid var(--red);transform:rotate(45deg)}
.work-photo{left:451px;top:2141px;width:327px;height:301px;background:radial-gradient(ellipse at 50% 55%,#3f7cff 0%,#28407a 30%,#4c5260 60%,#9aa1ac 100%)}

/* footer */
.footer{left:0;top:2510px;width:1200px;height:383px}
.foot-nav{top:2628px;display:flex;gap:22px;font-size:16px;font-weight:600;white-space:nowrap}
.divider{left:112px;width:976px;height:1px;background:#3a3d44}
.info{top:2718px;display:flex;gap:12px}
.info svg{flex:none}
.info-label{font-size:17px;line-height:22px}
.info-text{font-size:15.5px;line-height:26px;white-space:nowrap}
.copyright{left:0;top:2855px;width:1200px;text-align:center;font-size:16px}
</style>
</head>
<body>

<!-- header -->
<header class="abs site-header">
  <svg class="abs topbar" width="1200" height="28" viewBox="0 0 1200 28"><polygon points="427,0 1200,0 1200,28 452,28" fill="#e8262d"/></svg>
  <div class="abs topbar-text">+1800-555-0142 : CONTACT US</div>
  <div class="abs brand"><span class="brand-dot"></span>BBSA</div>
  <nav class="abs nav" style="right:274px"><a>Home</a><span class="sep">|</span><a>About</a><span class="sep">|</span><a>Why Laser</a><span class="sep">|</span><a>Capabilities</a></nav>
  <a class="abs btn btn-blue" style="left:959px;top:38px;width:130px;height:44px">Get A Quote</a>
</header>

<!-- hero -->
<section>
  <div class="abs hero-photo" role="img" aria-label="Laser cutting head firing onto a metal sheet with sparks"></div>
  <div class="abs hero-glow"></div>
  <div class="abs hero-kicker">WELCOME TO</div>
  <h1 class="abs hero-title">BRIGHTFORM BEAM SERVICES AUSTRALIA</h1>
  <div class="abs hero-line"></div>
  <a class="abs btn btn-red" style="left:548px;top:356px;width:104px;height:44px">Explore</a>
</section>

<!-- about -->
<section>
  <div class="abs about-bg" role="img" aria-label="Dim industrial workshop background"></div>
  <svg class="abs" style="left:0;top:500px" width="1200" height="80" viewBox="0 0 1200 80">
    <polygon points="0,0 1200,0 1200,7 600,75 0,7" fill="#1b5f6e"/>
    <polygon points="0,7 600,64 1200,7 1200,18 600,75 0,18" fill="#1a73c4"/>
  </svg>
  <h2 class="abs about-title">ABOUT US</h2>
  <div class="abs rule" style="left:112px;top:667px;background:var(--blue)"></div>
  <div class="abs rule" style="left:172px;top:667px;background:var(--red)"></div>
  <p class="abs about-text">Background Information - Brightform Beam Services Australia (BBSA) is a leading provider of advanced laser restoration services for the residential, commercial, medical, hazardous and industrial sectors, offering waste free, chemical free and damage free complete restoration of metals, concrete, wood, stone and heritage, hygiene and hazard surfaces, with complete removal of coatings, bacteria, paint, rust, graffiti, mold and fire ash (soot), and preparation and treating for welding and bonding.</p>
  <a class="abs btn btn-blue" style="left:112px;top:950px;width:120px;height:45px">Learn More</a>
  <svg class="abs" style="left:719px;top:623px" width="360" height="362" viewBox="0 0 360 362">
    <polyline points="210,22 210,2 2,2 2,232 26,232" fill="none" stroke="#e8262d" stroke-width="4"/>
    <polyline points="331,125 353,125 353,357 331,357" fill="none" stroke="#1a73c4" stroke-width="4"/>
  </svg>
  <div class="abs about-photo" role="img" aria-label="Laser nozzle working over a metal surface"></div>
</section>

<!-- why choose us -->
<section>
  <div class="abs why-bg" role="img" aria-label="Blue-toned industrial machinery background"></div>
  <h2 class="abs section-title" style="top:1099px">WHY CHOOSE US</h2>
  <div class="abs rule" style="left:543px;top:1159px;background:var(--blue)"></div>
  <div class="abs rule" style="left:603px;top:1159px;background:var(--red)"></div>

  <div class="abs card" style="left:112px">
    <svg width="34" height="34" viewBox="0 0 34 34"><rect x="4" y="6" width="26" height="24" fill="none" stroke="#1a73c4" stroke-width="2"/><path d="M22 12 L13 21 M13 15 V21 H19" stroke="#e8262d" stroke-width="2" fill="none"/></svg>
    <span>Minimum<br>Downtime</span>
  </div>
  <div class="abs card" style="left:311px">
    <svg width="36" height="34" viewBox="0 0 36 34"><path d="M18 4 L33 30 H3 Z" fill="none" stroke="#1a73c4" stroke-width="2"/><path d="M11 24 H25" stroke="#e8262d" stroke-width="3"/></svg>
    <span>No Surface<br>Damage</span>
  </div>
  <div class="abs card" style="left:511px">
    <svg width="34" height="34" viewBox="0 0 34 34"><circle cx="16" cy="17" r="13" fill="none" stroke="#1a73c4" stroke-width="2"/><path d="M5 13 H27 M5 21 H27" stroke="#1a73c4" stroke-width="1.5"/><circle cx="25" cy="25" r="4" fill="#fff" stroke="#e8262d" stroke-width="2"/></svg>
    <span>No Environm-<br>ental Impact</span>
  </div>
  <div class="abs card" style="left:710px">
    <svg width="34" height="34" viewBox="0 0 34 34"><circle cx="17" cy="17" r="14" fill="none" stroke="#e8262d" stroke-width="2"/><rect x="11" y="10" width="12" height="15" fill="none" stroke="#1a73c4" stroke-width="2"/><path d="M7 27 L27 7" stroke="#e8262d" stroke-width="2"/></svg>
    <span>No Mess,<br>No Waste</span>
  </div>
  <div class="abs card" style="left:909px">
    <svg width="34" height="34" viewBox="0 0 34 34"><path d="M6 20 A12 12 0 0 1 26 8" fill="none" stroke="#e8262d" stroke-width="2"/><path d="M28 14 A12 12 0 0 1 8 26" fill="none" stroke="#e8262d" stroke-width="2"/><circle cx="17" cy="17" r="5" fill="none" stroke="#1a73c4" stroke-width="2"/></svg>
    <span>Complete<br>Restoration</span>
  </div>
</section>

<!-- industries -->
<section>
  <div class="abs ind-bg" role="img" aria-label="Dark workshop background with tools"></div>
  <h2 class="abs section-title" style="top:1476px">INDUSTRIES</h2>
  <div class="abs rule" style="left:543px;top:1536px;background:var(--blue)"></div>
  <div class="abs rule" style="left:603px;top:1536px;background:var(--red)"></div>

  <div class="abs ind-card ind-blue" style="left:112px" role="img" aria-label="Hospital operating theatre">
    <div class="abs ind-label">Medical/Sterile</div></div>
  <div class="abs ind-card ind-red" style="left:361px" role="img" aria-label="Hotel lobby with luggage trolley">
    <div class="abs ind-label">Hospitality</div></div>
  <div class="abs ind-card ind-blue" style="left:611px" role="img" aria-label="Building under construction with scaffolding">
    <div class="abs ind-label">Construction</div></div>
  <div class="abs ind-card ind-red" style="left:861px" role="img" aria-label="City skyline with tower cranes">
    <div class="abs ind-label">Infrastructure</div></div>

  <svg class="abs arrow" style="left:48px" width="16" height="28" viewBox="0 0 16 28"><path d="M13 3 L3 14 L13 25" fill="none" stroke="#9aa0aa" stroke-width="2.5"/></svg>
  <svg class="abs arrow" style="left:1131px" width="16" height="28" viewBox="0 0 16 28"><path d="M3 3 L13 14 L3 25" fill="none" stroke="#ffffff" stroke-width="2.5"/></svg>
</section>

<!-- we work on -->
<section>
  <div class="abs work-bg" role="img" aria-label="Glowing red machined metal parts in the dark"></div>
  <h2 class="abs section-title" style="top:2026px">WE WORK ON</h2>
  <div class="abs rule" style="left:543px;top:2086px;background:var(--blue)"></div>
  <div class="abs rule" style="left:603px;top:2086px;background:var(--red)"></div>

  <div class="abs list-head" style="left:118px;top:2174px">Contaminants:</div>
  <ul class="abs list" style="left:118px;top:2233px">
    <li>Bacteria</li><li>Rust</li><li>Corrosion</li><li>Oxides</li><li>Grease</li><li>Oil</li><li>Paint</li>
  </ul>
  <ul class="abs list" style="left:272px;top:2233px">
    <li>Stains</li><li>Mold</li><li>Soot / Carbon</li><li>Graffiti</li><li>Coatings</li><li>Dirt</li><li>Residue</li>
  </ul>

  <svg class="abs" style="left:436px;top:2350px" width="300" height="108" viewBox="0 0 300 108"><polyline points="3,3 3,104 296,104 296,90" fill="none" stroke="#1a73c4" stroke-width="4"/></svg>
  <div class="abs work-photo" role="img" aria-label="Laser machine engraving a metal plate with blue light"></div>

  <div class="abs list-head" style="left:829px;top:2174px">Surfaces:</div>
  <ul class="abs list" style="left:829px;top:2233px">
    <li>Metals</li><li>Engines</li><li>Tools</li><li>Machinery</li><li>Blockwork</li><li>Concrete</li><li>Paint</li>
  </ul>
  <ul class="abs list" style="left:983px;top:2233px">
    <li>Stone</li><li>Wood</li><li>Aluminium</li>
  </ul>
</section>

<!-- footer -->
<footer>
  <svg class="abs footer" width="1200" height="383" viewBox="0 0 1200 383">
    <polygon points="0,68 600,10 1200,68 1200,383 0,383" fill="#131417"/>
    <polygon points="0,68 600,0 1200,68 1200,80 600,18 0,80" fill="#e8262d"/>
  </svg>
  <div class="abs brand" style="left:125px;top:2608px"><span class="brand-dot"></span>BBSA</div>
  <nav class="abs foot-nav" style="right:112px"><a>Home</a><span>|</span><a>About</a><span>|</span><a>Why Laser</a><span>|</span><a>Capabilities</a><span>|</span><a>Contact</a></nav>
  <div class="abs divider" style="top:2683px"></div>

  <div class="abs info" style="left:110px">
    <svg width="20" height="26" viewBox="0 0 20 26"><path d="M10 24 C4 16 2 12 2 9 A8 8 0 0 1 18 9 C18 12 16 16 10 24Z" fill="none" stroke="#fff" stroke-width="1.8"/><circle cx="10" cy="9" r="3" fill="none" stroke="#fff" stroke-width="1.8"/></svg>
    <div><div class="info-label">ADDRESS</div><div class="info-text">BBSA,<br>Addres Comes Here</div></div>
  </div>
  <div class="abs info" style="left:385px">
    <svg width="24" height="20" viewBox="0 0 24 20"><rect x="1.5" y="2" width="21" height="16" fill="none" stroke="#fff" stroke-width="1.8"/><path d="M2 3 L12 11 L22 3" fill="none" stroke="#fff" stroke-width="1.8"/></svg>
    <div><div class="info-label">EMAIL</div><div class="info-text">info@bbsa.example</div></div>
  </div>
  <div class="abs info" style="left:623px">
    <svg width="22" height="22" viewBox="0 0 22 22"><path d="M5 2 L9 6 L7 9 C8 12 10 14 13 15 L16 13 L20 17 L17 20 C9 19 3 13 2 5 Z" fill="none" stroke="#fff" stroke-width="1.8"/></svg>
    <div><div class="info-label">PHONE</div><div class="info-text">+1800-555-0142</div></div>
  </div>
  <div class="abs info" style="left:877px">
    <svg width="22" height="22" viewBox="0 0 22 22"><circle cx="11" cy="11" r="9" fill="none" stroke="#fff" stroke-width="2"/><path d="M11 6 V11 H15" fill="none" stroke="#fff" stroke-width="2"/></svg>
    <div><div class="info-label">HOURS</div><div class="info-text">Mon - Fri&nbsp; 8:30am - 9pm</div></div>
  </div>

  <div class="abs divider" style="top:2828px"></div>
  <div class="abs copyright">2023 Brightform Beam Services Australia. All Rights Reserved.</div>
</footer>

</body>
</html>
```